Various Designs

We need various designs for our new hand disinfectant dispensers that feature three extra-large windows that allow users to customize the appearance simply by changing the graphics.
Each dispenser has one window at the front and one on each side. The front window can have two different sizes. Please refer to attached zip file named Dispenser_Design_Templates.
The designs should be fresh and of high quality. Please don't just place a photo and spam me.
The design should also contain our logo (PVM Switzerland - is included in the template).
The design should further be professional enough for a medical and public setting. The dispensers will be used in hospitals, medical facilities, old pension homes, schools, restaurants, kitchens, public places etc.
We value creativity a lot!
It would be great if the dispenser features a slogan such as "Hand Hygiene Saves Lives". I have added a number of slogans at the end of this description.
Do not use dark colors such as brown. These colors do not stand for hygiene. You can use black but only in conjunction with a bright color.
The following files contain designs that I like:
- 01w
- velunadecor
- worldwide
- IMG_0137
Slogans:
- Hand Hygiene Saves Lives
- Did you wash your hands?
- Did you disinfect your hands?
- Protect Yourself and Your Patients
- Healthy Hands Start Here
- Hand Hygiene We Love... We Care... We Share...
- Clean hands prevent germs from spreading.
- Practice Good Hand Hygiene
- Save Lives: Clean Your Hands
- Save Lives: Disinfect Your Hands
- Washing Hands Saves Lives
- Wash Your Hands Please
- Be aware…..!!!!! Wash with care…..!!!!!
- Hand Hygiene Station
- Hand Hygiene Share your care, not your germs
- Good Hand Hygiene It's Critical Sanitize Wash Moisturize
- Disinfect (image of a hand)
- Clean (image of a hand)
- No Water? No Problem. Waterless Hand Rub. Keep it Handy.
- Wash your hands! If not for yourself, then do it for them.
- Practice good hygiene - it-s contagious!
- Be aware, wash with care!
- Filthy fingers forecast sickness and sadness.
- Hand Hygiene The power is in your hands
- Bury the germ, Wash your hands
- Sanitize your hands and support our clean hands initiative
- Sanitize your hands. Together we can make a difference.
- You are grand if you wash your hand.
- Holding hands feels better when they’re clean.
- Be wise wash hands often.
- Wash those germs away!!!
- Your Hands Can Be Dangerous. Disinfect them to keep germs away.
- Ten out of ten patients prefer care from clean hands.
- Safety first, disinfect and protect
- It’s universal- handwashing every patient every time!
- Infection control is in your hands.
- Make your intention prevention. Wash your hands

```html
<!DOCTYPE html>
<html lang="en">
<head>
<meta charset="utf-8">
<title>PVM Switzerland – Dispenser Window Graphics</title>
<link href="https://fonts.googleapis.com/css2?family=Titan+One&display=swap" rel="stylesheet">
<style>
  :root {
    --canvas: #ffffff;
    --paper: #f6f9fc;
    --paper-mist: #edf3f8;
    --paper-grey: #e6ecf2;
    --water-foam: #e4f0f6;
    --water-light: #bcdcec;
    --water-mid: #86c0de;
    --water-deep: #4b95cc;
    --water-teal: #5db6ad;
    --water-green: #8cc7b4;
    --cut-line: #d8262c;
    --safe-line: #6db33f;
    --brand-blue: #2f5fa8;
    --slogan-fill: #c6e2f7;
    --slogan-edge: #3d72b8;
  }
  * { margin: 0; padding: 0; box-sizing: border-box; }
  html, body { width: 1200px; height: 1000px; overflow: hidden; background: var(--canvas); }
  .sheet { position: relative; width: 1200px; height: 1000px; overflow: hidden; }

  .window-art {
    position: absolute;
    top: 67px;
    height: 865px;
  }
  .window-art--left {
    left: 0; width: 297px;
    background:
      radial-gradient(ellipse 140px 40px at 120px 700px, rgba(134,192,222,0.55), transparent 70%),
      radial-gradient(ellipse 160px 50px at 90px 820px, rgba(93,182,173,0.55), transparent 70%),
      radial-gradient(ellipse 120px 30px at 220px 760px, rgba(75,149,204,0.35), transparent 70%),
      radial-gradient(ellipse 160px 90px at 60px 350px, rgba(230,236,242,0.8), transparent 70%),
      linear-gradient(178deg, var(--paper) 0%, var(--paper-mist) 64%, var(--water-foam) 66.5%, var(--water-light) 72%, var(--water-mid) 83%, var(--water-green) 92%, var(--water-teal) 100%);
  }
  .window-art--front {
    left: 392px; width: 422px;
    background:
      radial-gradient(ellipse 110px 50px at 300px 40px, rgba(200,210,222,0.6), transparent 70%),
      radial-gradient(ellipse 150px 35px at 250px 620px, rgba(75,149,204,0.45), transparent 70%),
      radial-gradient(ellipse 200px 40px at 200px 740px, rgba(75,149,204,0.4), transparent 70%),
      radial-gradient(ellipse 150px 40px at 60px 800px, rgba(93,182,173,0.45), transparent 70%),
      radial-gradient(ellipse 200px 35px at 330px 830px, rgba(60,130,200,0.5), transparent 70%),
      linear-gradient(176deg, var(--paper) 0%, var(--paper-mist) 58%, var(--water-foam) 61%, var(--water-light) 67%, var(--water-mid) 80%, var(--water-deep) 100%);
  }
  .window-art--right {
    left: 903px; width: 297px;
    background:
      radial-gradient(ellipse 120px 30px at 90px 700px, rgba(93,182,173,0.45), transparent 70%),
      radial-gradient(ellipse 160px 40px at 180px 830px, rgba(60,130,200,0.55), transparent 70%),
      radial-gradient(ellipse 60px 40px at 60px 530px, rgba(140,199,180,0.5), transparent 70%),
      radial-gradient(ellipse 140px 80px at 200px 200px, rgba(230,236,242,0.8), transparent 70%),
      linear-gradient(180deg, var(--paper) 0%, var(--paper-mist) 55%, var(--water-foam) 56.5%, var(--water-light) 62%, var(--water-mid) 78%, var(--water-deep) 100%);
  }

  .template-lines { position: absolute; inset: 0; width: 1200px; height: 1000px; }
  .cut-line { fill: none; stroke: var(--cut-line); stroke-width: 1.3; }
  .safe-line { fill: none; stroke: var(--safe-line); stroke-width: 1.3; }
  .mount-hole { fill: none; stroke: var(--cut-line); stroke-width: 1.3; }

  .brand {
    position: absolute;
    left: 488px; top: 198px;
    display: flex; align-items: flex-end; gap: 14px;
    font-family: "Titan One", sans-serif;
    font-weight: 400;
    color: var(--brand-blue);
  }
  .brand__name { font-size: 44px; line-height: 1; letter-spacing: 4px; }
  .brand__country { font-size: 15px; line-height: 1; padding-bottom: 8px; }

  .slogan {
    position: absolute;
    left: 425px; width: 360px; top: 306px;
    text-align: center;
    font-family: "Titan One", sans-serif;
    font-size: 22.5px;
    line-height: 32px;
    color: var(--slogan-fill);
    -webkit-text-stroke: 1.2px var(--slogan-edge);
    paint-order: stroke fill;
  }
</style>
</head>
<body>
<main class="sheet">
  <div class="window-art window-art--left" role="img" aria-label="Watercolour paper texture fading into soft blue-green sea water at the bottom"></div>
  <div class="window-art window-art--front" role="img" aria-label="Watercolour paper texture fading into soft blue sea water at the bottom"></div>
  <div class="window-art window-art--right" role="img" aria-label="Watercolour paper texture fading into soft blue sea water at the bottom"></div>

  <svg class="template-lines" viewBox="0 0 1200 1000" aria-hidden="true">
    <!-- left side window -->
    <path class="cut-line" d="M20 78 L252 82 Q265 84 266 97 L290 906 Q290 918 278 918 L75 918 L62 770 Q55 690 38 640 Q20 590 20 550 Z"/>
    <path class="safe-line" d="M23 100 L240 102 Q258 104 259 122 L272 872 Q272 893 250 894 L92 897 Q82 897 81 887 L69 775 Q62 705 46 655 Q25 600 23 550 Z"/>
    <circle class="mount-hole" cx="45" cy="89" r="5"/>
    <circle class="mount-hole" cx="252" cy="98" r="5"/>
    <circle class="mount-hole" cx="99" cy="908" r="5"/>
    <circle class="mount-hole" cx="265" cy="900" r="5"/>

    <!-- front window -->
    <path class="cut-line" d="M408 78 L797 78 L776 903 L460 903 Z"/>
    <path class="safe-line" d="M440 175 Q440 112 490 104 Q600 92 718 102 Q765 108 765 160 L742 842 Q740 872 712 875 Q600 893 492 875 Q468 870 467 842 Z"/>
    <circle class="mount-hole" cx="433" cy="106" r="5"/>
    <circle class="mount-hole" cx="771" cy="106" r="5"/>
    <circle class="mount-hole" cx="481" cy="876" r="5"/>
    <circle class="mount-hole" cx="724" cy="876" r="5"/>

    <!-- right side window -->
    <path class="cut-line" d="M942 84 L1178 78 L1178 555 Q1176 610 1158 650 Q1146 690 1140 760 L1122 916 L922 918 Q910 918 910 905 L928 98 Q930 86 942 84 Z"/>
    <path class="safe-line" d="M958 100 L1172 100 L1172 560 Q1169 615 1150 657 Q1138 700 1133 770 L1120 884 Q1118 894 1108 894 L948 895 Q926 893 926 872 L936 122 Q938 102 958 100 Z"/>
    <circle class="mount-hole" cx="943" cy="98" r="5"/>
    <circle class="mount-hole" cx="1151" cy="89" r="5"/>
    <circle class="mount-hole" cx="931" cy="899" r="5"/>
    <circle class="mount-hole" cx="1097" cy="908" r="5"/>
  </svg>

  <div class="brand">
    <span class="brand__name">PVM</span>
    <span class="brand__country">Switzerland</span>
  </div>

  <p class="slogan">Be<br>Hygiene Serene.<br>Keep Your Hands Clean.</p>
</main>
</body>
</html>
```